Email Signature Design

Please design an email signature, the below is an example of our current design;
___

HARCOURT ESTATE PARTNERS PTY LTD
DOMINIC FARRADAY
Licensed Strata and Community Manager

148 Calloway Street,
ULTIMO NSW 2007

P: 02.9374.6082 F: 9463.7820
Website: www.harcourtestate.com.au

This e-mail message and accompanying data may contain information that is confidential and private. If you are not the intended recipient, the use, dissemination, distribution or copying of this message or data is prohibited.

If you have received this e-mail in error please notify us immediately and delete all material pertaining to this e-mail. strata@harcourtestate.com.au

___

We would like to incorporate our logo and company colours, you can view the colours and feel of image at www.harcourtestate.com.au

Industry/Entity Type

It Company

Requirements
Must have
• use of logo and company colours (image)

```html
<!DOCTYPE html>
<html lang="en">
<head>
<meta charset="utf-8">
<title>Harcourt Estate Partners – Email Signature</title>
<link rel="stylesheet" href="https://fonts.googleapis.com/css2?family=Source+Sans+3:wght@400;600;700&display=swap">
<style>
  :root {
    --olive: #7f7d3c;
    --slate: #6d6e70;
    --sand: #e0d1a8;
    --ink: #2b2b2b;
    --paper: #ffffff;
    --backdrop: #efefef;
  }
  * { margin: 0; padding: 0; box-sizing: border-box; }
  html, body {
    width: 1200px; height: 440px; overflow: hidden;
    background: var(--backdrop);
    font-family: "Source Sans 3", "Myriad Pro", Arial, sans-serif;
  }
  .signature {
    position: relative; width: 1200px; height: 440px;
    background: var(--paper); overflow: hidden;
  }
  .accent-band {
    position: absolute; left: 0; right: 0; top: 250px; bottom: 0;
    background: linear-gradient(90deg,
      var(--paper) 0%, var(--paper) 44%,
      var(--sand) 54%, var(--olive) 64%, var(--olive) 100%);
  }
  .brand {
    position: absolute; left: 109px; top: 204px;
    display: flex; align-items: center; gap: 12px;
  }
  .brand-square { width: 22px; height: 22px; background: var(--olive); }
  .brand-name {
    font-weight: 700; font-size: 27px; letter-spacing: 0.5px;
    color: var(--olive); line-height: 1;
  }
  .company {
    position: absolute; left: 109px; top: 282px;
    font-size: 23px; color: var(--olive); line-height: 1.1;
  }
  .address {
    position: absolute; left: 109px; top: 318px;
    font-size: 23px; color: var(--ink); line-height: 1.1;
  }
  .person {
    position: absolute; right: 35px; top: 46px; text-align: right;
  }
  .person-name {
    font-weight: 700; font-size: 22px; color: var(--olive); letter-spacing: 0.3px;
  }
  .person-title { font-size: 23px; color: var(--slate); margin-top: 2px; }
  .contacts {
    position: absolute; right: 35px; top: 272px;
    list-style: none; text-align: right; color: var(--paper);
    font-size: 22px; line-height: 41px;
  }
  .contacts li { display: flex; justify-content: flex-end; align-items: center; gap: 10px; }
  .contacts svg { width: 18px; height: 18px; fill: var(--paper); }
</style>
</head>
<body>
<div class="signature">
  <div class="accent-band" role="img" aria-label="Decorative flowing band in sand, grey and olive tones"></div>

  <div class="brand">
    <span class="brand-square"></span>
    <span class="brand-name">HARCOURT ESTATE PARTNERS</span>
  </div>

  <p class="company">HARCOURT ESTATE PARTNERS PTY LTD</p>
  <p class="address">148 Calloway Street, ULTIMO NSW 2007</p>

  <div class="person">
    <p class="person-name">DOMINIC FARRADAY</p>
    <p class="person-title">Licensed Strata and Community Manager</p>
  </div>

  <ul class="contacts">
    <li><svg viewBox="0 0 24 24"><path d="M6.6 10.8a15 15 0 0 0 6.6 6.6l2.2-2.2a1 1 0 0 1 1-.25 11.4 11.4 0 0 0 3.6.57 1 1 0 0 1 1 1V20a1 1 0 0 1-1 1A17 17 0 0 1 3 4a1 1 0 0 1 1-1h3.5a1 1 0 0 1 1 1c0 1.25.2 2.45.57 3.57a1 1 0 0 1-.25 1z"/></svg>02.9374.6082</li>
    <li><svg viewBox="0 0 24 24"><path d="M7 3h10v5H7zM4 9h16a2 2 0 0 1 2 2v6h-4v4H6v-4H2v-6a2 2 0 0 1 2-2zm4 7v3h8v-3z"/></svg>9463.7820</li>
    <li><svg viewBox="0 0 24 24"><path d="M2 6h20v12H2zm2 2v.5l8 5 8-5V8l-8 5z"/></svg>strata@harcourtestate.com.au</li>
    <li><svg viewBox="0 0 24 24"><path d="M12 2a10 10 0 1 0 0 20 10 10 0 0 0 0-20zm-1 2.1V8H7.6A8 8 0 0 1 11 4.1zm2 0A8 8 0 0 1 16.4 8H13zM6.7 10H11v4H6.7a8 8 0 0 1 0-4zm6.3 0h4.3a8 8 0 0 1 0 4H13zm-5.4 6H11v3.9A8 8 0 0 1 7.6 16zm5.4 0h3.4a8 8 0 0 1-3.4 3.9z"/></svg>www.harcourtestate.com.au</li>
  </ul>
</div>
</body>
</html>
```